Heron Loan Partners Business Card

We need a business card design for our mortgage servicing company. In addition to servicing the loans of homeowners, we help homeowners with purchasing their homes and any mortgage refinancing. We would like to see designs that use the colors in the logo attached below (gold-ish yellow and navy blue), and any other design you deem fit! The design should communicate a simpler life with smart mortgages provided by Heron.

```html
<!DOCTYPE html>
<html lang="en">
<head>
<meta charset="utf-8">
<title>Heron Loan Partners – Business Card</title>
<link href="https://fonts.googleapis.com/css2?family=Open+Sans:wght@400;700&display=swap" rel="stylesheet">
<style>
  :root {
    --page-bg: #d8d1c5;
    --card-bg: #ebe5d9;
    --card-edge: #f6f1e8;
    --navy: #1c1646;
    --navy-deep: #140f36;
    --navy-soft: #3a3463;
    --gold: #d6a02c;
    --gold-text: #d4a23a;
    --cream: #e6dccb;
    --muted: #c6bfb2;
  }
  * { margin: 0; padding: 0; box-sizing: border-box; }
  html, body { width: 1200px; height: 1046px; overflow: hidden; }
  body {
    background: var(--page-bg);
    font-family: "Open Sans", Arial, sans-serif;
    position: relative;
  }
  .business-card {
    position: absolute;
    left: 60px; top: 228px;
    width: 1080px; height: 589px;
    border-radius: 30px;
    overflow: hidden;
    background: var(--card-bg);
    box-shadow: 0 0 0 2px var(--card-edge), 0 18px 40px rgba(60, 45, 25, 0.25);
  }
  .card-waves { position: absolute; inset: 0; width: 100%; height: 100%; }
  .brand {
    position: absolute;
    left: 560px; top: 88px;
    display: flex; align-items: center; gap: 14px;
  }
  .brand-dot {
    width: 22px; height: 22px; border-radius: 50%;
    background: var(--gold);
  }
  .brand-name {
    font-weight: 700; font-size: 40px; line-height: 1;
    color: var(--navy);
    white-space: nowrap;
  }
  .holder-name {
    position: absolute; left: 31px; top: 226px;
    font-size: 40px; font-weight: 700; color: var(--gold-text);
    white-space: nowrap;
  }
  .holder-title {
    position: absolute; left: 31px; top: 280px;
    font-size: 28px; color: var(--muted);
  }
  .address {
    position: absolute; left: 31px; top: 334px;
    font-size: 28px; line-height: 36px; color: var(--muted);
  }
  .contact-list {
    position: absolute; left: 30px; top: 442px;
    list-style: none;
  }
  .contact-item {
    display: flex; align-items: center; gap: 16px;
    height: 35.5px;
    font-size: 28px; color: var(--muted);
  }
  .contact-icon { width: 24px; height: 24px; flex: none; }
</style>
</head>
<body>
  <div class="business-card">
    <svg class="card-waves" viewBox="0 0 1610 878" preserveAspectRatio="none" aria-hidden="true">
      <defs>
        <linearGradient id="navyPanel" x1="0" y1="0" x2="1" y2="0">
          <stop offset="0" stop-color="#3b3562"/>
          <stop offset="0.3" stop-color="#2f2958"/>
          <stop offset="0.6" stop-color="#1a1440"/>
          <stop offset="1" stop-color="#140f36"/>
        </linearGradient>
      </defs>
      <path d="M0,92 C520,92 1000,578 1610,578 L1610,878 L0,878 Z" fill="var(--navy)"/>
      <path d="M0,100 C520,100 1000,638 1610,638 L1610,878 L0,878 Z" fill="var(--cream)"/>
      <path d="M0,108 C520,108 1000,652 1610,652 L1610,878 L0,878 Z" fill="var(--gold)"/>
      <path d="M0,178 C520,178 1000,716 1610,716 L1610,878 L0,878 Z" fill="var(--cream)"/>
      <path d="M0,190 C520,190 1000,732 1610,732 L1610,878 L0,878 Z" fill="url(#navyPanel)"/>
      <rect x="0" y="870" width="1610" height="8" fill="var(--gold)"/>
    </svg>

    <div class="brand">
      <span class="brand-dot"></span>
      <span class="brand-name">Heron Loan Partners</span>
    </div>

    <h1 class="holder-name">Lena Hartwell</h1>
    <p class="holder-title">Co-Founder</p>
    <p class="address">418 Meadowbrook Ave. Suite 310<br>Brookfield, TX 75091</p>

    <ul class="contact-list">
      <li class="contact-item">
        <svg class="contact-icon" viewBox="0 0 24 24" aria-hidden="true"><path fill="var(--gold)" d="M6.6 10.8a15.1 15.1 0 0 0 6.6 6.6l2.2-2.2a1 1 0 0 1 1-.25 11.4 11.4 0 0 0 3.6.57 1 1 0 0 1 1 1V20a1 1 0 0 1-1 1A17 17 0 0 1 3 4a1 1 0 0 1 1-1h3.5a1 1 0 0 1 1 1c0 1.25.2 2.45.57 3.57a1 1 0 0 1-.25 1z"/></svg>
        <span>(555) 214-3860</span>
      </li>
      <li class="contact-item">
        <svg class="contact-icon" viewBox="0 0 24 24" aria-hidden="true"><path fill="var(--gold)" d="M2 9l10-6 10 6v12H2z"/><path fill="var(--navy)" d="M3.5 10.2l8.5 5.3 8.5-5.3V19.5h-17z" opacity="0.35"/><path fill="none" stroke="var(--navy-deep)" stroke-width="1.2" d="M2.5 9.5l9.5 6 9.5-6"/></svg>
        <span>info@website.com</span>
      </li>
      <li class="contact-item">
        <svg class="contact-icon" viewBox="0 0 24 24" aria-hidden="true"><circle cx="12" cy="12" r="10" fill="var(--gold)"/><path fill="none" stroke="var(--navy-deep)" stroke-width="1.3" d="M2 12h20M12 2c3 3 3 17 0 20M12 2c-3 3-3 17 0 20"/></svg>
        <span>www.website.com</span>
      </li>
    </ul>
  </div>
</body>
</html>
```